THE WELLNESS BARN WEBSITE for Physio, Fitness, health

An attractive website advertising a physiotherapyand fitness / gym business, not generic, colours are natural, greens, browns, beiges. No cheesy pictures. With the ability to sell a small,amount of goods online if i decide to. Simple to navigate. Text boxes that i can input the main information and change easily. Somewhere to put my timetable. Easy to find contact details. However many pages it needs, im not fussed.
Target Market(s)
People looking for rehabilitation or fitness classes
Industry/Entity Type
Physiotherapy, Fitness, Gym, Health
Coding
Coded - Design and coding required
Number of Pages Required
1 page
Font styles to use
Other font styles liked:
- Im not fusse,ld, not script
Requirements
Must have
- Will upload posts from my business insta page for reference about the feel. Earthy natural tones, I have a lot of timber, and rustic looking piece's, plants etc in my clinic
Nice to have
- Simple to navigate
Should not have
- Cheesy "yoga" or generic "people doing physio" pics

```html
<!DOCTYPE html>
<html lang="en">
<head>
<meta charset="utf-8">
<title>The Wellness Barn Hervey Bay</title>
<link rel="stylesheet" href="https://fonts.googleapis.com/css2?family=Oswald:wght@500;600;700&family=Inter:ital,wght@0,400;0,500;0,600;0,700;1,500&display=swap">
<style>
:root{
  --green:#26421f;
  --green-deep:#1f3619;
  --green-band:#284522;
  --ink:#1d1d1b;
  --text:#444;
  --white:#fff;
  --footer:#1b1b1b;
  --line:#d6d6d6;
}
*{box-sizing:border-box;margin:0;padding:0}
html,body{width:1200px;height:4295px;overflow:hidden}
body{font-family:"Inter",sans-serif;color:var(--text);background:var(--white);position:relative}
.abs{position:absolute}
h1,h2{font-family:"Oswald",sans-serif;font-weight:600;color:var(--ink);letter-spacing:.3px}
.btn{display:inline-flex;align-items:center;justify-content:center;gap:10px;font-size:13px;font-weight:600;text-transform:uppercase;border-radius:6px;text-decoration:none}
.btn svg{width:14px;height:14px}
.btn-green{background:var(--green);color:var(--white)}
/* nav */
.site-nav{top:0;left:0;width:1200px;height:78px;background:var(--white)}
.nav-link{top:23px;height:29px;line-height:29px;font-size:13px;font-weight:500;color:var(--ink);text-transform:uppercase}
.nav-link.active{background:var(--green);color:var(--white);border-radius:15px;padding:0 14px}
.brand{top:14px;left:540px;width:120px;text-align:center;font-weight:700;font-size:15px;line-height:1.15;color:var(--green);display:flex;flex-direction:column;align-items:center;gap:6px}
.brand .dot{width:14px;height:14px;border-radius:50%;background:var(--green)}
.nav-phone{top:18px;left:882px;width:171px;height:44px;font-size:12px}
.nav-phone svg{width:12px;height:12px}
/* hero */
.hero{top:78px;left:0;width:1200px;height:574px;background:
  linear-gradient(180deg,rgba(20,16,12,.55) 0%,rgba(20,16,12,.35) 45%,rgba(15,12,10,.75) 100%),
  linear-gradient(180deg,#4e4338 0%,#6b5a48 38%,#3d342b 70%,#1c1814 100%)}
.hero-inner{top:140px;left:0;width:1200px;text-align:center;color:var(--white)}
.hero h1{color:var(--white);font-size:44px;letter-spacing:1px}
.hero p{font-size:16px;line-height:32px;margin-top:18px}
.hero em{display:block;font-size:16px;font-weight:500;margin-top:14px}
.hero .btn{margin-top:28px;width:166px;height:48px;border:2px solid #e8e8e8;color:var(--white);background:var(--green)}
/* about */
.about-photo{top:733px;left:145px;width:405px;height:400px;background:linear-gradient(180deg,#7a7672 0%,#5d5a57 45%,#2d2c2e 100%)}
.about-text{top:785px;left:622px;width:440px;text-align:center}
.about-text h2{font-size:38px}
.about-text p{font-size:12.5px;line-height:24px;margin-top:18px}
.about-text p+p{margin-top:4px}
.about-text .btn{margin-top:26px;width:143px;height:44px}
/* offer */
.offer-head{top:1200px;left:0;width:1200px;text-align:center}
.offer-head h2{font-size:37px}
.offer-head .rule{width:152px;height:4px;background:var(--green);margin:16px auto 0}
.offer-head p{width:920px;margin:30px auto 0;font-size:16px;line-height:32px}
.service{width:600px;height:427px;color:var(--white);text-align:center}
.service .label{position:absolute;left:0;width:600px;top:346px;font-size:16px;font-weight:500;text-transform:uppercase}
.service .chev{position:absolute;left:292px;top:385px;width:16px;height:16px}
.s1{top:1437px;left:0;background:linear-gradient(180deg,rgba(0,0,0,0) 55%,rgba(0,0,0,.45) 100%),linear-gradient(135deg,#cfd2cd,#959d97 50%,#5f6d6b)}
.s2{top:1437px;left:600px;background:linear-gradient(180deg,rgba(0,0,0,0) 55%,rgba(0,0,0,.4) 100%),linear-gradient(135deg,#6a4530,#3d2c23 55%,#201b18)}
.s3{top:1864px;left:0;background:linear-gradient(180deg,rgba(0,0,0,0) 55%,rgba(0,0,0,.45) 100%),linear-gradient(135deg,#524b46,#302c29 55%,#5a463b)}
.s4{top:1864px;left:600px;background:linear-gradient(135deg,#2e4c26,#1e3a1a 60%,#16301a)}
.s4 h3{position:absolute;top:120px;left:0;width:600px;font-size:16px;font-weight:500;text-transform:uppercase}
.s4 p{position:absolute;top:158px;left:110px;width:380px;font-size:13px;line-height:24px}
.s4 .btn{position:absolute;top:259px;left:215px;width:144px;height:42px;background:var(--white);color:var(--ink)}
/* team */
.team-head{top:2360px;left:145px}
.team-head h2{font-size:37px;display:flex;align-items:center;gap:18px}
.team-head h2 span{display:block;width:88px;height:4px;background:var(--green)}
.team-head p{font-size:15px;margin-top:14px}
.team-btn{top:2403px;left:902px;width:153px;height:44px}
.member{top:2490px;width:295px;height:280px}
.member .photo{width:295px;height:280px}
.member .tag{position:absolute;left:26px;top:247px;width:243px;height:62px;background:var(--white);text-align:center;padding-top:14px}
.member .tag strong{display:block;font-size:16px;font-weight:500;color:var(--ink)}
.member .tag small{display:block;font-size:10px;margin-top:8px}
/* stories */
.stories{top:2875px;left:0;width:1200px;height:477px;background:var(--green-band);overflow:hidden}
.stories-head{top:70px;left:0;width:1200px;text-align:center;color:var(--white)}
.stories-head h2{color:var(--white);font-size:37px;display:flex;justify-content:center;align-items:center;gap:20px}
.stories-head h2 span{display:block;width:86px;height:3px;background:var(--white)}
.stories-head p{font-size:16px;margin-top:16px}
.review{top:187px;width:295px;height:225px;background:var(--white);padding:28px 20px 0}
.review.faded{opacity:.12}
.stars{display:flex;gap:3px}
.stars svg{width:15px;height:15px}
.quote-mark{position:absolute;top:26px;right:20px;font-family:"Oswald",sans-serif;font-size:40px;line-height:1;color:#d9d9d9}
.review p{font-size:12px;line-height:24px;margin-top:16px}
.reviewer{position:absolute;left:20px;top:152px;display:flex;align-items:center;gap:14px}
.avatar{width:50px;height:50px;border-radius:50%;background:linear-gradient(160deg,#c7a48a,#7a5a47)}
.reviewer strong{display:block;font-size:14px;font-weight:500;color:var(--ink);text-transform:uppercase}
.reviewer small{display:block;font-size:10.5px;margin-top:6px}
/* faq */
.faq-photo{top:3428px;left:0;width:438px;height:465px;background:linear-gradient(180deg,#5e5852 0%,#3c3833 45%,#25262a 80%,#1d1e22 100%)}
.faq-head{top:3462px;left:530px}
.faq-head h2{font-size:37px;display:flex;align-items:center;gap:24px}
.faq-head h2 span{display:block;width:88px;height:4px;background:var(--green)}
.faq-item{left:530px;width:526px;border:1px solid var(--line);border-radius:24px;height:48px;display:flex;align-items:center;justify-content:space-between;padding:0 12px 0 22px;font-size:15px;font-weight:500;color:var(--ink)}
.faq-item svg{width:22px;height:22px}
.faq-open{left:530px;top:3670px;width:526px;height:136px;background:var(--green);border-radius:16px;color:var(--white);padding:18px 22px}
.faq-open .q{display:flex;justify-content:space-between;font-size:15px;font-weight:500}
.faq-open p{font-size:11.5px;line-height:24px;margin-top:8px;width:460px}
.faq-link{top:3836px;left:538px;font-size:15px;font-weight:500;color:var(--ink)}
/* footer */
.footer{top:3958px;left:0;width:1200px;height:337px;background:var(--footer);color:var(--white)}
.footer-brand{top:68px;left:145px;display:flex;align-items:center;gap:12px;font-weight:700;font-size:22px;line-height:1.1}
.footer-brand .dot{width:18px;height:18px;border-radius:50%;background:var(--white)}
.foot-col h4{font-size:14px;font-weight:500;text-transform:uppercase}
.foot-col ul{list-style:none;margin-top:8px}
.foot-col li{font-size:12px;line-height:21px;display:flex;gap:12px;align-items:center}
.foot-col li::before{content:"»";font-size:12px}
.contact-row{display:flex;gap:10px;align-items:center;font-size:12px;line-height:20px;margin-top:14px}
.contact-row .ic{width:24px;height:24px;flex:none;border:1.5px solid var(--white);border-radius:50%;display:flex;align-items:center;justify-content:center}
.contact-row .ic svg{width:12px;height:12px}
.foot-rule{top:224px;left:143px;width:914px;height:1px;background:#3a3a3a}
.copyright{top:246px;left:0;width:1200px;text-align:center;font-size:12px}
.socials{top:278px;left:0;width:1200px;display:flex;justify-content:center;gap:12px}
.socials span{width:27px;height:27px;border-radius:50%;border:1.5px solid var(--white)}
.socials span.on{background:var(--green)}
</style>
</head>
<body>

<header class="site-nav abs">
  <a class="nav-link active abs" style="left:145px">Home</a>
  <a class="nav-link abs" style="left:237px">About</a>
  <a class="nav-link abs" style="left:322px">Services</a>
  <a class="nav-link abs" style="left:428px">Team</a>
  <div class="brand abs"><span class="dot"></span>THE WELLNESS BARN</div>
  <a class="nav-link abs" style="left:700px">FAQs</a>
  <a class="nav-link abs" style="left:778px">Contact</a>
  <a class="btn btn-green nav-phone abs"><svg viewBox="0 0 24 24" fill="currentColor"><path d="M6.6 10.8a15 15 0 0 0 6.6 6.6l2.2-2.2a1 1 0 0 1 1-.25 11.4 11.4 0 0 0 3.6.57 1 1 0 0 1 1 1V20a1 1 0 0 1-1 1A17 17 0 0 1 3 4a1 1 0 0 1 1-1h3.5a1 1 0 0 1 1 1c0 1.25.2 2.45.57 3.6a1 1 0 0 1-.25 1z"/></svg>+61 400 555 218</a>
</header>

<section class="hero abs" role="img" aria-label="Dim timber-framed gym interior with rings, racks and training equipment">
  <div class="hero-inner abs">
    <h1>WELCOME TO THE WELLNESS BARN HERVEY BAY</h1>
    <p>Discover A Healthier You With Our Physiotherapist Led Programs. At The Wellness Barn Hervey Bay,<br>We Focus On Safe and Effective Movement To Enhance Your Quality Of Life.</p>
    <em>JOIN US FOR A COMPREHENSIVE APPROACH TO WELLBEING</em>
    <a class="btn"><span>Get Started</span><svg viewBox="0 0 24 24" fill="none" stroke="currentColor" stroke-width="2.5"><path d="M7 17 17 7M8 7h9v9"/></svg></a>
  </div>
</section>

<div class="about-photo abs" role="img" aria-label="The clinic team standing together inside the gym"></div>
<section class="about-text abs">
  <h2>ABOUT THE WELLNESS BARN</h2>
  <p>At The Wellness Barn Hervey Bay, we are dedicated to empowering individuals through safe and effective movement. Our mission is enhance your health and wellbeing with professional support.</p>
  <p>We aim to empower individuals to achieve their health and wellness goals through safe and effective movement,</p>
  <a class="btn btn-green">Read More<svg viewBox="0 0 24 24" fill="none" stroke="currentColor" stroke-width="2.5"><path d="M7 17 17 7M8 7h9v9"/></svg></a>
</section>

<section class="offer-head abs">
  <h2>WHAT DO WE HAVE TO OFFER?</h2>
  <div class="rule"></div>
  <p>The Wellness Barn Hervey Bay is dedicated to empowering individuals to achieve their health and wellbeing goals through safe and effective movement,Our core values include Integrity, Collaboration, Inclusivity, and a strong Commitment to health,We believe in providing professional support tailored to each individual's needs.</p>
</section>

<div class="service s1 abs" role="img" aria-label="Group physiotherapy class in a bright studio">
  <span class="label">Physiotherapy Classes For Everyone</span>
  <svg class="chev" viewBox="0 0 16 16" fill="none" stroke="#fff" stroke-width="1.6"><path d="M4 10l4-4 4 4"/></svg>
</div>
<div class="service s2 abs" role="img" aria-label="Practitioner guiding a client through a wellness plan">
  <span class="label">Holistic Wellness Programs</span>
  <svg class="chev" viewBox="0 0 16 16" fill="none" stroke="#fff" stroke-width="1.6"><path d="M4 10l4-4 4 4"/></svg>
</div>
<div class="service s3 abs" role="img" aria-label="Nutrition consultation at a kitchen table">
  <span class="label">Personalized Nutrition Guidance</span>
  <svg class="chev" viewBox="0 0 16 16" fill="none" stroke="#fff" stroke-width="1.6"><path d="M4 10l4-4 4 4"/></svg>
</div>
<div class="service s4 abs" role="img" aria-label="Mindfulness session under a green overlay">
  <h3>Mindfulness and Yoga Sessions</h3>
  <p>Slow down with guided breathing, gentle mobility and mindful stretching that help you move freely and feel calm and grounded.</p>
  <a class="btn">Read More<svg viewBox="0 0 24 24" fill="none" stroke="currentColor" stroke-width="2.5"><path d="M7 17 17 7M8 7h9v9"/></svg></a>
</div>

<section class="team-head abs">
  <h2>MEET OUR TEAM <span></span></h2>
  <p>Discover the dedicated professionals committed to your health.</p>
</section>
<a class="btn btn-green team-btn abs">Learn More<svg viewBox="0 0 24 24" fill="none" stroke="currentColor" stroke-width="2.5"><path d="M7 17 17 7M8 7h9v9"/></svg></a>

<div class="member abs" style="left:145px">
  <div class="photo" role="img" aria-label="Portrait of the lead physiotherapist in a bright clinic" style="background:linear-gradient(160deg,#ece5db,#c7b5a1 60%,#a9957f)"></div>
  <div class="tag"><strong>Dr. Clara Whitfield</strong><small>Lead Physiotherapist</small></div>
</div>
<div class="member abs" style="left:452px">
  <div class="photo" role="img" aria-label="Portrait of the wellness coach in a library corner" style="background:linear-gradient(160deg,#9a968e,#5b5c5c 55%,#3a3e43)"></div>
  <div class="tag"><strong>Jonah Reyes</strong><small>Wellness Coach</small></div>
</div>
<div class="member abs" style="left:760px">
  <div class="photo" role="img" aria-label="Portrait of the physiotherapy assistant in scrubs" style="background:linear-gradient(160deg,#ddd0b2,#a6a397 50%,#5b7aa0)"></div>
  <div class="tag"><strong>Mia Tran</strong><small>Physiotherapy Assistant</small></div>
</div>

<section class="stories abs">
  <div class="stories-head abs">
    <h2><span></span>CLIENT SUCCESS STORIES<span></span></h2>
    <p>Hear From Our Clients About Their Transformative Journeys With Us</p>
  </div>

  <div class="review faded abs" style="left:-165px"></div>
  <div class="review abs" style="left:145px">
    <div class="stars"><svg viewBox="0 0 24 24" fill="#e9b62a"><path d="M12 2l3 7h7l-5.5 4.5 2 7.5L12 17l-6.5 4 2-7.5L2 9h7z"/></svg><svg viewBox="0 0 24 24" fill="#e9b62a"><path d="M12 2l3 7h7l-5.5 4.5 2 7.5L12 17l-6.5 4 2-7.5L2 9h7z"/></svg><svg viewBox="0 0 24 24" fill="#e9b62a"><path d="M12 2l3 7h7l-5.5 4.5 2 7.5L12 17l-6.5 4 2-7.5L2 9h7z"/></svg><svg viewBox="0 0 24 24" fill="#e9b62a"><path d="M12 2l3 7h7l-5.5 4.5 2 7.5L12 17l-6.5 4 2-7.5L2 9h7z"/></svg><svg viewBox="0 0 24 24" fill="#e9b62a"><path d="M12 2l3 7h7l-5.5 4.5 2 7.5L12 17l-6.5 4 2-7.5L2 9h7z"/></svg></div>
    <span class="quote-mark">”</span>
    <p>The Wellness Barn has completely changed my approach to fitness. Their programs are tailored and effective!</p>
    <div class="reviewer"><span class="avatar" role="img" aria-label="Client photo"></span><div><strong>Harper Lowe</strong><small>Fitness Enthusiast</small></div></div>
  </div>
  <div class="review abs" style="left:452px">
    <div class="stars"><svg viewBox="0 0 24 24" fill="#e9b62a"><path d="M12 2l3 7h7l-5.5 4.5 2 7.5L12 17l-6.5 4 2-7.5L2 9h7z"/></svg><svg viewBox="0 0 24 24" fill="#e9b62a"><path d="M12 2l3 7h7l-5.5 4.5 2 7.5L12 17l-6.5 4 2-7.5L2 9h7z"/></svg><svg viewBox="0 0 24 24" fill="#e9b62a"><path d="M12 2l3 7h7l-5.5 4.5 2 7.5L12 17l-6.5 4 2-7.5L2 9h7z"/></svg><svg viewBox="0 0 24 24" fill="#e9b62a"><path d="M12 2l3 7h7l-5.5 4.5 2 7.5L12 17l-6.5 4 2-7.5L2 9h7z"/></svg><svg viewBox="0 0 24 24" fill="#e9b62a"><path d="M12 2l3 7h7l-5.5 4.5 2 7.5L12 17l-6.5 4 2-7.5L2 9h7z"/></svg></div>
    <span class="quote-mark">”</span>
    <p>I never thought I could regain my mobility. The physiotherapy classes here are a game changer!</p>
    <div class="reviewer"><span class="avatar" role="img" aria-label="Client photo"></span><div><strong>Grant Ellison</strong><small>Retired Veteran</small></div></div>
  </div>
  <div class="review abs" style="left:760px">
    <div class="stars"><svg viewBox="0 0 24 24" fill="#e9b62a"><path d="M12 2l3 7h7l-5.5 4.5 2 7.5L12 17l-6.5 4 2-7.5L2 9h7z"/></svg><svg viewBox="0 0 24 24" fill="#e9b62a"><path d="M12 2l3 7h7l-5.5 4.5 2 7.5L12 17l-6.5 4 2-7.5L2 9h7z"/></svg><svg viewBox="0 0 24 24" fill="#e9b62a"><path d="M12 2l3 7h7l-5.5 4.5 2 7.5L12 17l-6.5 4 2-7.5L2 9h7z"/></svg><svg viewBox="0 0 24 24" fill="#e9b62a"><path d="M12 2l3 7h7l-5.5 4.5 2 7.5L12 17l-6.5 4 2-7.5L2 9h7z"/></svg><svg viewBox="0 0 24 24" fill="#e9b62a"><path d="M12 2l3 7h7l-5.5 4.5 2 7.5L12 17l-6.5 4 2-7.5L2 9h7z"/></svg></div>
    <span class="quote-mark">”</span>
    <p>I love how the wellness programs fit into my hectic schedule. I feel healthier and more energetic!</p>
    <div class="reviewer"><span class="avatar" role="img" aria-label="Client photo"></span><div><strong>Sophie Marsh</strong><small>Busy Mom</small></div></div>
  </div>
  <div class="review faded abs" style="left:1068px"></div>
</section>

<div class="faq-photo abs" role="img" aria-label="Group of class members standing together in the gym"></div>
<section class="faq-head abs"><h2>FAQS <span></span></h2></section>
<div class="faq-item abs" style="top:3537px">What types of programs do you offer?<svg viewBox="0 0 24 24"><circle cx="12" cy="12" r="10" fill="#1d1d1b"/><path d="M10 7l5 5-5 5" fill="none" stroke="#fff" stroke-width="2.4"/></svg></div>
<div class="faq-item abs" style="top:3603px">How can I get started?<svg viewBox="0 0 24 24"><circle cx="12" cy="12" r="10" fill="#1d1d1b"/><path d="M10 7l5 5-5 5" fill="none" stroke="#fff" stroke-width="2.4"/></svg></div>
<div class="faq-open abs">
  <div class="q"><span>Are your classes suitable for beginners?</span><svg width="22" height="22" viewBox="0 0 24 24"><circle cx="12" cy="12" r="10" fill="#fff"/><path d="M7 10l5 5 5-5" fill="none" stroke="#26421f" stroke-width="2.4"/></svg></div>
  <p>Absolutely! Our classes are designed to accommodate all fitness levels, and our qualified physiotherapists provide personalized support to ensure everyone can participate safely.</p>
</div>
<a class="faq-link abs">View Programs &nbsp;»</a>

<footer class="footer abs">
  <div class="footer-brand abs"><span class="dot"></span><span>THE WELLNESS<br>BARN</span></div>
  <div class="foot-col abs" style="left:493px;top:52px">
    <h4>Pages</h4>
    <ul><li>About Us</li><li>Programs</li><li>Testimonials</li><li>Contact</li></ul>
  </div>
  <div class="foot-col abs" style="left:807px;top:52px">
    <h4>Contact Us</h4>
    <div class="contact-row"><span class="ic"><svg viewBox="0 0 24 24" fill="#fff"><path d="M6.6 10.8a15 15 0 0 0 6.6 6.6l2.2-2.2a1 1 0 0 1 1-.25 11.4 11.4 0 0 0 3.6.57 1 1 0 0 1 1 1V20a1 1 0 0 1-1 1A17 17 0 0 1 3 4a1 1 0 0 1 1-1h3.5a1 1 0 0 1 1 1c0 1.25.2 2.45.57 3.6a1 1 0 0 1-.25 1z"/></svg></span>+61 400 555 218</div>
    <div class="contact-row"><span class="ic"><svg viewBox="0 0 24 24" fill="none" stroke="#fff" stroke-width="2.4"><rect x="3" y="5" width="18" height="14" rx="2"/><path d="M3 7l9 6 9-6"/></svg></span>hello@wellnessbarn.com</div>
    <div class="contact-row"><span class="ic"><svg viewBox="0 0 24 24" fill="none" stroke="#fff" stroke-width="2.4"><path d="M12 22s7-7 7-12a7 7 0 0 0-14 0c0 5 7 12 7 12z"/><circle cx="12" cy="10" r="2.5"/></svg></span>18 Ridgeback Lane, Pialba,<br>QLD, Australia, Queensland</div>
  </div>
  <div class="foot-rule abs"></div>
  <p class="copyright abs">© 2025 &nbsp;The Wellness Barn Hervey Bay &nbsp;| &nbsp;All Rights Reserved</p>
  <div class="socials abs"><span></span><span class="on"></span></div>
</footer>

</body>
</html>
```